Business Card for Coastal Tundrabridge Advisory

We need a business card for Coastal Tundrabridge Advisory. The company website address is provided below. The company logo is attached. We provide specialized permafrost services to the mining, transportation, and oil & gas industries. The card should be prepared for:
Matthias Korhonen, PhD.
Coastal Tundrabridge Advisory
PO Box 418259
Quillwater, Alaska 99642
Direct: +1-907-555-0143
Email: mkorhonen@tundrabridgeadvisory.example
Website: www.coastaltundrabridgeadvisory.example

```html
<!DOCTYPE html>
<html lang="en">
<head>
<meta charset="utf-8">
<title>Coastal Tundrabridge Advisory – Business Card</title>
<link rel="stylesheet" href="https://fonts.googleapis.com/css2?family=Montserrat:wght@400;500;700&display=swap">
<style>
  :root {
    --backdrop: #e9e6e1;
    --card-white: #ffffff;
    --card-navy: #1b222c;
    --card-navy-light: #2e3744;
    --ink: #2a2f36;
    --ink-soft: #5a6069;
    --rule: #9aa0a8;
    --on-navy: #f2f4f6;
    --on-navy-soft: #b9c0c8;
  }
  * { box-sizing: border-box; margin: 0; padding: 0; }
  html, body { width: 1200px; height: 913px; overflow: hidden; }
  body {
    background: var(--backdrop);
    font-family: "Montserrat", sans-serif;
    color: var(--ink);
    position: relative;
  }
  .card {
    position: absolute;
    width: 525px;
    height: 300px;
    top: 306px;
    border-radius: 3px;
    box-shadow: 0 10px 28px rgba(0,0,0,0.18);
    overflow: hidden;
  }
  .card-front { left: 50px; background: var(--card-white); }
  .card-back {
    left: 625px;
    background: linear-gradient(150deg, var(--card-navy) 0%, var(--card-navy) 45%, var(--card-navy-light) 100%);
  }
  .accent-bar { position: absolute; width: 26px; background: var(--card-navy); }
  .accent-bar.top-right { right: 0; top: 0; height: 120px; }
  .accent-bar.bottom-left { left: 0; bottom: 0; height: 118px; }

  .front-wordmark {
    position: absolute;
    left: 46px;
    top: 186px;
    width: 190px;
    font-weight: 700;
    font-size: 15px;
    line-height: 1.25;
    letter-spacing: 0.04em;
    text-transform: uppercase;
    color: var(--ink);
  }
  .divider {
    position: absolute;
    left: 250px;
    top: 52px;
    width: 1px;
    height: 196px;
    background: var(--rule);
  }
  .details { position: absolute; left: 266px; top: 54px; width: 240px; }
  .name { font-weight: 700; font-size: 15px; color: var(--ink); }
  .role { font-size: 10.5px; color: var(--ink-soft); margin-top: 3px; }
  .address { font-size: 10.5px; color: var(--ink-soft); margin-top: 7px; line-height: 1.4; }
  .contacts { list-style: none; margin-top: 14px; }
  .contacts li {
    display: flex;
    align-items: center;
    gap: 8px;
    font-size: 9.5px;
    color: var(--ink-soft);
    line-height: 1;
    margin-bottom: 9px;
    white-space: nowrap;
  }
  .contacts svg { width: 10px; height: 10px; flex: none; fill: var(--ink); }

  .back-wordmark {
    position: absolute;
    left: 0; right: 0;
    top: 50%;
    transform: translateY(-50%);
    text-align: center;
    font-weight: 500;
    font-size: 22px;
    letter-spacing: 0.12em;
    line-height: 1.5;
    text-transform: uppercase;
    color: var(--on-navy);
  }
</style>
</head>
<body>
  <section class="card card-front" aria-label="Business card front">
    <span class="accent-bar top-right"></span>
    <span class="accent-bar bottom-left"></span>
    <p class="front-wordmark">Coastal Tundrabridge Advisory</p>
    <span class="divider"></span>
    <div class="details">
      <h1 class="name">Matthias Korhonen, PhD.</h1>
      <p class="role">Managing Director</p>
      <p class="address">PO Box 418259<br>Quillwater, Alaska 99642</p>
      <ul class="contacts">
        <li>
          <svg viewBox="0 0 24 24" aria-hidden="true"><path d="M6.6 10.8a15.1 15.1 0 0 0 6.6 6.6l2.2-2.2a1 1 0 0 1 1-.25 11.4 11.4 0 0 0 3.6.57 1 1 0 0 1 1 1V20a1 1 0 0 1-1 1A17 17 0 0 1 3 4a1 1 0 0 1 1-1h3.5a1 1 0 0 1 1 1c0 1.25.2 2.45.57 3.6a1 1 0 0 1-.25 1z"/></svg>
          +1-907-555-0143
        </li>
        <li>
          <svg viewBox="0 0 24 24" aria-hidden="true"><path d="M2 5h20v14H2z M2 5l10 8 10-8" fill="none" stroke="#2a2f36" stroke-width="2.4"/></svg>
          mkorhonen@tundrabridgeadvisory.example
        </li>
        <li>
          <svg viewBox="0 0 24 24" aria-hidden="true"><g fill="none" stroke="#2a2f36" stroke-width="2"><circle cx="12" cy="12" r="10"/><ellipse cx="12" cy="12" rx="4.5" ry="10"/><path d="M2 12h20"/></g></svg>
          www.coastaltundrabridgeadvisory.example
        </li>
      </ul>
    </div>
  </section>

  <section class="card card-back" aria-label="Business card back">
    <p class="back-wordmark">Coastal Tundrabridge<br>Advisory</p>
  </section>
</body>
</html>
```